vorne matcha

I'm a local business called 'VORNE' and will be sourcing organic ceremonial grade matcha tea through a private labeler in Japan. I need a sleek layout for the label that wraps around the tin that holds the 30g of matcha. I have samples of inspiration and designs that I like. This is very high end matcha so I would like for it to have an expensive look. I also have the dimensions of the label for the tin to show. I have specifics of things that need to be on the label, so please let me know if you need any of that information at this point!

Target Market(s)

High end matcha tea drinkers. The label files I sent are what my eye was drawn to.

Industry/Entity Type

matcha

Font styles to use
Other font styles liked:
• I like the font styles of the samples I uploaded in the photos

Colors

Designer to choose only greyscale colors for use in the design.

Requirements
Must have
• In the biggest lettering of them all in the center is MATCHA. (everything capitalized).Above it, my brand name which is VORNE. and if it looks good, Vorne no.7 like the Duvelle no.5.below the MATCHA, I would like it to say Ceremonial Grade.Another thing... Design wise!I would like the tin to be silver, and the label to be a sort of creme, in between white color with black lettering. Also, I would like the font to be more along the lines of the Ma Verte fonts I sent you... the files that show the cologne bottle with the silver top, creme label, and lettering:)Thanks so much and can't to see what you doOn it as well, the USDA certified organic label, which is in one of the screenshots I uploaded.There needs to be the net weight which is 30g. and also that it is sourced in Uji, Japanmy website on the back: www.saptamatcha.comThe nutrition facts and how to use I will send later:)
Nice to have
• my signature somewhere (like the coffee picture I sent)

```html
<!DOCTYPE html>
<html lang="en">
<head>
<meta charset="utf-8">
<title>Vorne No.7 Matcha – Tin Labels</title>
<link rel="stylesheet" href="https://fonts.googleapis.com/css2?family=Montserrat:wght@300;400;500;600;700&display=swap">
<style>
  :root {
    --canvas: #ffffff;
    --label: #1e1e1e;
    --label-edge: #262626;
    --ink: #f2f2f2;
    --ink-soft: #d6d6d6;
    --rule: #bdbdbd;
    --badge: #e6e6e6;
    --shadow: rgba(0, 0, 0, 0.28);
  }
  html, body {
    margin: 0;
    padding: 0;
    width: 1200px;
    height: 1001px;
    overflow: hidden;
    background: var(--canvas);
    font-family: "Montserrat", sans-serif;
    color: var(--ink);
  }
  .canvas {
    position: relative;
    width: 1200px;
    height: 1001px;
  }

  /* Lid label */
  .lid-label {
    position: absolute;
    left: 50px;
    top: 390px;
    width: 220px;
    height: 220px;
    border-radius: 50%;
    background: radial-gradient(circle at 50% 45%, var(--label-edge), var(--label) 70%);
    box-shadow: 0 18px 28px -14px var(--shadow);
    text-align: center;
  }
  .lid-label .series {
    position: absolute; left: 0; right: 0; top: 74px;
    font-size: 11px; font-weight: 400; letter-spacing: 0.02em;
  }
  .lid-label .product {
    position: absolute; left: 0; right: 0; top: 90px;
    font-size: 27px; font-weight: 600; letter-spacing: 0.03em; line-height: 1;
  }
  .lid-label .rule {
    position: absolute; left: 36px; right: 36px; height: 0;
    border-top: 1px solid var(--rule);
  }
  .lid-label .rule.upper { top: 133px; }
  .lid-label .rule.lower { top: 152px; }
  .lid-label .grade {
    position: absolute; left: 0; right: 0; top: 137px;
    font-size: 10.5px; font-weight: 400; letter-spacing: 0.03em; color: var(--ink-soft);
  }
  .lid-label .weight {
    position: absolute; left: 0; right: 0; top: 172px;
    font-size: 7px; font-weight: 400; letter-spacing: 0.05em; color: var(--ink-soft);
  }

  /* Wrap label */
  .wrap-label {
    position: absolute;
    left: 383px;
    top: 418px;
    width: 768px;
    height: 164px;
    background: var(--label);
    box-shadow: 0 26px 30px -20px var(--shadow);
  }
  .wrap-label .pattern-field {
    position: absolute; inset: 0;
    background: linear-gradient(180deg, var(--label-edge), var(--label));
  }

  .info-panel {
    position: absolute; left: 70px; width: 110px; top: 0; height: 100%;
    text-align: center;
  }
  .info-panel .signature {
    position: absolute; left: 22px; top: 34px; width: 66px; height: 18px;
    border-radius: 3px;
    background: linear-gradient(90deg, #3a3a3a, #4a4a4a, #3a3a3a);
  }
  .info-panel .website {
    position: absolute; left: 0; right: 0; top: 63px;
    font-size: 5.5px; color: var(--ink-soft);
  }
  .info-panel .badges {
    position: absolute; left: 0; right: 0; top: 75px;
    display: flex; justify-content: center; gap: 8px;
  }
  .info-panel .origin {
    position: absolute; left: 0; right: 0; top: 115px;
    font-size: 5.5px; color: var(--ink-soft);
  }
  .info-panel .net-weight {
    position: absolute; left: 0; right: 0; top: 126px;
    font-size: 7px; font-weight: 500; letter-spacing: 0.02em;
  }

  .front-panel {
    position: absolute; left: 263px; width: 180px; top: 0; height: 100%;
    text-align: center;
  }
  .front-panel .series {
    position: absolute; left: 0; right: 0; top: 44px;
    font-size: 11.5px; font-weight: 400; letter-spacing: 0.02em;
  }
  .front-panel .product {
    position: absolute; left: 0; right: 0; top: 61px;
    font-size: 29px; font-weight: 600; letter-spacing: 0.03em; line-height: 1;
  }
  .front-panel .rule {
    position: absolute; left: 5px; right: 5px; height: 0;
    border-top: 1px solid var(--rule);
  }
  .front-panel .rule.upper { top: 105px; }
  .front-panel .rule.lower { top: 126px; }
  .front-panel .grade {
    position: absolute; left: 0; right: 0; top: 109px;
    font-size: 10.5px; font-weight: 400; letter-spacing: 0.03em; color: var(--ink-soft);
  }

  .details-panel {
    position: absolute; left: 495px; width: 183px; top: 34px;
  }
  .details-panel .heading {
    display: flex; align-items: center; gap: 5px;
    font-size: 5.5px; font-weight: 600; letter-spacing: 0.04em;
    margin: 0 0 2px;
  }
  .details-panel .heading::after {
    content: ""; flex: 1; border-top: 0.6px solid var(--rule);
  }
  .details-panel .body {
    margin: 0 0 9px;
    font-size: 5.3px; line-height: 1.32; text-align: justify; color: var(--ink-soft);
  }
</style>
</head>
<body>
<main class="canvas">

  <section class="lid-label" aria-label="Lid label">
    <div class="series">VORNE NO.7</div>
    <div class="product">MATCHA</div>
    <div class="rule upper"></div>
    <div class="grade">CEREMONIAL GRADE</div>
    <div class="rule lower"></div>
    <div class="weight">30G</div>
  </section>

  <section class="wrap-label" aria-label="Wrap-around tin label">
    <div class="pattern-field" role="img" aria-label="Faint tone-on-tone floral pattern across the label"></div>

    <div class="info-panel">
      <div class="signature" role="img" aria-label="Handwritten owner signature"></div>
      <div class="website">www.vornematcha.com</div>
      <div class="badges">
        <svg width="30" height="30" viewBox="0 0 30 30" aria-label="Organic certification badge" role="img">
          <circle cx="15" cy="15" r="14" fill="none" stroke="var(--badge)" stroke-width="1.6"/>
          <circle cx="15" cy="15" r="9.5" fill="var(--badge)"/>
        </svg>
        <svg width="30" height="30" viewBox="0 0 30 30" aria-label="Japanese organic certification badge" role="img">
          <circle cx="15" cy="15" r="14" fill="none" stroke="var(--badge)" stroke-width="1.6"/>
        </svg>
      </div>
      <div class="origin">sourced in Uji, Japan</div>
      <div class="net-weight">NET WEIGHT: 30G</div>
    </div>

    <div class="front-panel">
      <div class="series">VORNE NO.7</div>
      <div class="product">MATCHA</div>
      <div class="rule upper"></div>
      <div class="grade">CEREMONIAL GRADE</div>
      <div class="rule lower"></div>
    </div>

    <div class="details-panel">
      <h3 class="heading">INGREDIENTS:</h3>
      <p class="body">100% shade-grown first harvest tencha leaves, stone ground into a fine powder. No added sugar, colour or fillers of any kind.</p>
      <h3 class="heading">HOW TO USE:</h3>
      <p class="body">Sift one scoop of matcha into a warm bowl. Add 70 ml of water at 80°C and whisk briskly in a zigzag motion until a fine, even foam forms on top. Enjoy at once, slowly.</p>
    </div>
  </section>

</main>
</body>
</html>
```